Web Design for Two by Two Organic Soap Company

We need a website design for the company Brevin Organics based on the package design per attached.

The design should communicate high end, luxury organic. The site will provide facts about how the spread of disease causes deaths and can be prevented with hand washing. The site will also have a page about why we are passionate about organics and how that relates to our skin including skin facts.
Also, the site should have an e-commerce product page and shopping cart.

Target Market(s)

Educated, health conscious and socially conscious consumers who shop luxury. Target vendors include Marlow Grocers and Tavelli..

Industry/Entity Type

E-Commerce

Font styles to use
Other font styles liked:
• See attached

Requirements
Must have
• Use of Ying Yang leaf Logo provided.
Based on design provided.

```html
<!DOCTYPE html>
<html lang="en">
<head>
<meta charset="utf-8">
<title>Brevin Organics – organic soap</title>
<link href="https://fonts.googleapis.com/css2?family=Dosis:wght@400;500;600&family=Ubuntu:wght@400;500&display=swap" rel="stylesheet">
<style>
:root{
  --page:#f3f3f3;
  --panel:#ffffff;
  --ink:#3a3a3a;
  --green:#6f9a10;
  --green-dark:#4f7a06;
  --green-light:#94bf2c;
  --brand:#3e5a1c;
  --brand-mark:#5f9b3f;
  --price:#d3241c;
  --rule:#b9b9b9;
  --hill:#8fba3a;
}
*{box-sizing:border-box;margin:0;padding:0}
html,body{width:1023px;height:1200px;overflow:hidden;background:var(--page);font-family:"Ubuntu",sans-serif;color:var(--ink)}
.canvas{position:relative;width:1023px;height:1200px;overflow:hidden}
.abs{position:absolute}
.header-scene{left:420px;top:0;width:603px;height:160px;background:radial-gradient(ellipse at 60% 10%,#bfdff2 0%,#dcebf3 45%,rgba(243,243,243,0) 75%)}
.brand-square{left:85px;top:40px;width:34px;height:34px;background:var(--brand-mark)}
.brand-name{left:130px;top:33px;font-family:"Dosis",sans-serif;font-weight:500;font-size:34px;line-height:46px;color:var(--brand)}
.nav{left:85px;top:125px;width:853px;height:39px;border-top:1px solid #999;border-bottom:1px solid #999;background:linear-gradient(#fff,#f4f4f4)}
.nav a{position:absolute;top:9px;transform:translateX(-50%);font-family:"Dosis",sans-serif;font-size:15px;letter-spacing:1px;color:#333;text-decoration:none}
.nav .active-bar{position:absolute;left:56px;top:-2px;width:75px;height:3px;background:var(--green)}
.panel{background:var(--panel);box-shadow:0 10px 10px -8px rgba(0,0,0,.25)}
.side-title{font-family:"Dosis",sans-serif;font-weight:400;font-size:15px;letter-spacing:.5px;color:#333;padding:8px 0 0 15px;height:37px;border-top:1px solid var(--green-dark);border-bottom:3px solid var(--green-light);background:#f6f6f6}
.side-row{margin:0 15px 0 17px;border-bottom:1px solid #ddd;font-family:"Dosis",sans-serif;font-size:12px;color:#555}
.side-row b{color:var(--green);font-weight:600}
.btn{display:block;text-align:center;color:#fff;font-family:"Dosis",sans-serif;font-size:17px;background:linear-gradient(#8fbe1e,#4f7f05);border:4px solid #fff;outline:1px solid #ccc;height:34px;line-height:26px}
.shop-list{list-style:none}
.shop-list li{margin:0 15px 0 17px;border-bottom:1px solid #ddd;height:26px;line-height:26px;font-family:"Dosis",sans-serif;font-size:12px;color:#555;padding-left:14px;position:relative}
.shop-list li::before{content:"";position:absolute;left:2px;top:11px;border-left:3px solid var(--green);border-top:2.5px solid transparent;border-bottom:2.5px solid transparent}
.slide-photo{background:linear-gradient(135deg,#b59a6a 0%,#8a7350 40%,#6b5a40 70%,#c2a878 100%)}
.release{background:rgba(108,150,10,.93);color:#fff}
.release h3,.events h3{font-family:"Dosis",sans-serif;font-weight:600;font-size:17px;letter-spacing:.5px}
.events{background:rgba(196,14,20,.93);color:#fff}
.dots span{display:inline-block;width:8px;height:8px;border-radius:50%;background:var(--green);margin-left:5px}
.dots span:first-child{background:#fff;border:1px solid #ddd}
.section-title{font-family:"Dosis",sans-serif;font-weight:400;font-size:15px;letter-spacing:1px;color:#333}
.product{top:597px;width:150px;height:253px;background:#fff}
.product .photo{position:absolute;left:14px;top:18px;width:135px;height:101px;border:1px solid var(--green-light)}
.product .name{position:absolute;left:20px;top:131px;font-family:"Dosis",sans-serif;font-size:14px;color:#333}
.product .price{position:absolute;left:20px;top:158px;font-family:"Dosis",sans-serif;font-size:14px;color:#333}
.product .price b{color:var(--price);font-weight:500}
.product .btn{position:absolute;left:14px;top:196px;width:116px}
.about-text{font-size:10.5px;line-height:13px;color:#444;letter-spacing:.2px}
.about-list{list-style:none;font-size:10.5px;color:#444}
.about-list li{position:relative;padding-left:10px;height:20.5px}
.about-list li::before{content:"";position:absolute;left:0;top:2px;border-left:3px solid var(--green);border-top:3px solid transparent;border-bottom:3px solid transparent}
.footer-scene{left:0;top:1060px;width:1023px;height:140px;background:linear-gradient(#f3f3f3 0%,#d5e9f3 30%,#bcd98a 62%,var(--hill) 80%,#6f9a2a 100%)}
.footer-nav{left:0;top:1146px;width:1023px;text-align:center;font-size:9.5px;letter-spacing:.5px;color:#333}
.footer-nav span{margin:0 5px}
.social{left:0;top:1172px;width:1023px;text-align:center;font-family:"Dosis",sans-serif;font-size:12px;color:#fff}
.social span{margin:0 9px}
</style>
</head>
<body>
<div class="canvas">

  <div class="abs header-scene" role="img" aria-label="Illustrated sky with clouds, green hills and young trees"></div>

  <div class="abs brand-square"></div>
  <div class="abs brand-name">Brevin Organics</div>

  <nav class="abs nav">
    <span class="active-bar"></span>
    <a href="#" style="left:89px">HOME</a>
    <a href="#" style="left:251px">ABOUT</a>
    <a href="#" style="left:409px">CONTACT</a>
    <a href="#" style="left:563px">STORES</a>
    <a href="#" style="left:735px">NATURAL SOAP</a>
  </nav>

  <section class="abs panel" style="left:85px;top:186px;width:222px;height:198px">
    <div class="side-title">Your Shoping</div>
    <div class="side-row" style="height:40px;line-height:40px">My Cart : <b>0</b> products</div>
    <div class="side-row" style="height:27px;line-height:27px">Organic bar soaps</div>
    <div class="side-row" style="height:29px;line-height:29px;border:none">Total : <b>$ 0</b></div>
    <a class="btn" style="position:absolute;left:53px;top:143px;width:116px">Details</a>
  </section>

  <section class="abs panel" style="left:85px;top:411px;width:222px;height:205px">
    <div class="side-title">Shop Online</div>
    <ul class="shop-list" style="margin-top:10px">
      <li>organic bar soaps</li>
      <li>castile liquid soaps</li>
      <li>organic balms &amp; oils</li>
      <li>unique handmade gifts</li>
      <li style="border:none">timber &amp; coal for men</li>
    </ul>
  </section>

  <section class="abs panel" style="left:85px;top:645px;width:222px;height:207px;border-top:1px solid var(--green-dark)">
    <div class="abs" role="img" aria-label="Video still of a customer washing with soap lather" style="left:0;top:10px;width:224px;height:171px;background:linear-gradient(135deg,#7d6e62,#c9b8a6 50%,#5e544c)"></div>
    <div class="abs" style="left:0;top:150px;width:224px;height:31px;background:rgba(0,0,0,.55)">
      <svg width="224" height="31"><polygon points="20,9 20,22 30,15.5" fill="#fff"/><rect x="55" y="15" width="135" height="4" fill="#666"/><rect x="55" y="15" width="4" height="4" fill="#fff"/><rect x="200" y="10" width="14" height="11" fill="#2aa8e0"/></svg>
    </div>
  </section>

  <section class="abs" style="left:325px;top:186px;width:613px;height:352px;background:#fff;border-bottom:1px solid #ccc">
    <div class="abs slide-photo" role="img" aria-label="Photo of soap packages and jars of balm" style="left:13px;top:13px;width:587px;height:327px"></div>
    <div class="abs release" style="left:313px;top:85px;width:262px;height:104px;padding:8px 16px">
      <h3>NEW RELEASES</h3>
      <p style="font-size:9px;line-height:12px;margin-top:5px;opacity:.9">Sed ut perspiciatis unde omnis iste natus error sit voluptatem accusantium doloremque laudantium, totam rem aperiam, eaque ipsa quae ab illo inventore</p>
      <p style="font-size:9px;color:#111;margin-top:5px">read more</p>
    </div>
    <div class="abs events" style="left:313px;top:204px;width:262px;height:100px;padding:8px 16px">
      <h3>UPCOMING EVENTS</h3>
      <div style="display:flex;font-size:9.5px;line-height:13px;margin-top:5px">
        <div style="width:120px"><b>when:</b><br>monday,March<br>12th,2014</div>
        <div><b>Location:</b><br>48 Alder Row<br>Fairhaven,CA<br>95517</div>
      </div>
    </div>
  </section>
  <div class="abs dots" style="left:868px;top:545px"><span></span><span></span><span></span><span></span><span></span></div>

  <h2 class="abs section-title" style="left:338px;top:570px">Feature Product</h2>
  <div class="abs" style="left:325px;top:593px;width:613px;border-top:1px solid var(--rule)"></div>

  <article class="abs product" style="left:325px">
    <div class="photo" role="img" aria-label="Lavender soap bars with herbs" style="background:linear-gradient(135deg,#c9b29a,#8d6d9e)"></div>
    <div class="name">organic bar soaps</div>
    <div class="price">Price : <b>$20</b></div>
    <a class="btn">Buy</a>
  </article>
  <article class="abs product" style="left:478px">
    <div class="photo" role="img" aria-label="Stack of cream and speckled soap bars" style="left:9px;background:linear-gradient(135deg,#f3e6b8,#e8c89a)"></div>
    <div class="name" style="left:19px">organic bar soaps</div>
    <div class="price" style="left:19px">Price : <b>$20</b></div>
    <a class="btn" style="left:19px;width:113px">Buy</a>
  </article>
  <article class="abs product" style="left:632px">
    <div class="photo" role="img" aria-label="Essential oil bottle with orange flower" style="left:3px;background:linear-gradient(135deg,#c46a1a,#4a2a10)"></div>
    <div class="name" style="left:11px">organic bar soaps</div>
    <div class="price" style="left:11px">Price : <b>$20</b></div>
    <a class="btn" style="left:16px;width:116px">Buy</a>
  </article>
  <article class="abs product" style="left:786px;width:152px">
    <div class="photo" role="img" aria-label="Yellow herbal soap bars" style="left:0;background:linear-gradient(135deg,#e6cf6a,#d9d3b0)"></div>
    <div class="name" style="left:5px">organic bar soaps</div>
    <div class="price" style="left:5px">Price : <b>$20</b></div>
    <a class="btn" style="left:16px;width:116px">Buy</a>
  </article>

  <h2 class="abs section-title" style="left:98px;top:876px">About</h2>
  <div class="abs" style="left:86px;top:903px;width:852px;border-top:1px solid var(--rule)"></div>
  <p class="abs about-text" style="left:88px;top:916px;width:850px">Lorem ipsum dolor sit amet, consectetur adipiscing elit. Nulla at dui vitae metus fringilla congue eget et libero. Vivamus lobortis, metus placerat euismod dictum, justo purus eleifend leo, ac imperdiet ipsum dui at mauris.Pellentesque volutpat adipiscing tristique. Nullam varius felis lorem, nec adipiscing nisi. In nisl ipsum, aliquet sit amet auctor nec, facilisis ac dolor. Fusce pulvinar volutpat leo, eu iaculis leo rutrum eu. Nullam ultrices ultrices massa, a sollicitudin elit lobortis eget. Integer id rutrum velit. Nam pellentesque scelerisque felis non tempus.</p>
  <ul class="abs about-list" style="left:88px;top:977px">
    <li>Lorem ipsum dolor sit amet, consectetur adipiscing elit.</li>
    <li>Nulla at dui vitae metus fringilla congue egeteto purus emperdiet ipsum dui at mauris.</li>
    <li>Lorem ipsum dolor sit arus emperdiet ipsuonsectetur adipiscing elit.</li>
  </ul>
  <div class="abs" style="left:97px;top:1040px;font-size:9px;font-weight:500;color:var(--green-dark)">- MORE INFO -</div>

  <div class="abs footer-scene" role="img" aria-label="Illustrated green hills with young trees under a light sky"></div>
  <nav class="abs footer-nav">
    <span>HOME</span>|<span>ABOUT</span>|<span>CONTACT</span>|<span>STORES</span>|<span>NATURAL SOAP</span>
  </nav>
  <div class="abs social"><span>Frondly</span><span>Netlace</span><span>Clipreel</span></div>

</div>
</body>
</html>
```